Website for Excavator and Earthworks Company

We require a modern, sleek and practical website for our newly created earthworks/excavator business in Perth, Western Australia called Bluegum Ridge Earthworks.

The website should have a modern, cutting edge feel but only needs to be relatively simplistic in it's layout and eventual functionality.

Some pages it should have would be Home, About, Projects and Contact Us.

```html
<!DOCTYPE html>
<html lang="en">
<head>
<meta charset="utf-8">
<title>Bluegum Ridge Earthworks</title>
<link href="https://fonts.googleapis.com/css2?family=Orbitron:wght@700;800&family=Rubik:wght@400;500&display=swap" rel="stylesheet">
<style>
:root{
  --lime:#cddc00;
  --navy:#1e2c3b;
  --ink:#111;
  --white:#fff;
  --grey:#f2f2f2;
  --muted:#444;
}
*{box-sizing:border-box;margin:0;padding:0}
html,body{width:1200px;height:4024px;overflow:hidden}
body{position:relative;background:var(--white);font-family:"Rubik",sans-serif;color:var(--ink)}
.abs{position:absolute}
.display{font-family:"Orbitron",sans-serif;font-weight:800;text-transform:uppercase;letter-spacing:1px;line-height:1.15}
.btn{position:absolute;display:flex;align-items:center;justify-content:center;font-family:"Rubik",sans-serif;font-weight:500;font-size:12px;text-transform:uppercase;letter-spacing:.5px;clip-path:polygon(6% 0,100% 0,94% 100%,0 100%)}
.btn.lime{background:var(--lime);color:var(--ink)}
.btn.white{background:var(--white);color:var(--ink)}
.btn.black{background:var(--ink);color:var(--white);clip-path:none}
.brand{position:absolute;display:flex;align-items:center;gap:10px;font-family:"Rubik",sans-serif;font-weight:500;font-size:15px;text-transform:uppercase;color:var(--ink);letter-spacing:.5px}
.brand .mark{width:26px;height:26px;background:var(--lime)}
.nav{position:absolute;display:flex;gap:26px;font-weight:500;font-size:11px;text-transform:uppercase}
.photo{position:absolute}
/* header */
.header{left:55px;top:13px;width:1093px;height:60px;background:var(--white);clip-path:polygon(0 0,98.5% 0,100% 100%,0 100%)}
/* hero */
.hero{left:0;top:0;width:1200px;height:667px;clip-path:polygon(0 0,100% 0,100% 86.2%,0 100%);background:linear-gradient(160deg,#4d4a44 0%,#6b5d3f 35%,#5a4a32 60%,#3a2f24 100%)}
.hero-title{left:0;width:1200px;text-align:center;color:var(--white);font-size:38px}
.hero-sub{left:0;width:1200px;text-align:center;color:var(--white);font-size:12.5px}
/* about */
.about-title{left:180px;top:740px;font-size:33px}
.about-rule{left:180px;top:831px;width:470px;height:2px;background:var(--lime)}
.about-text{left:180px;width:330px;font-size:11px;line-height:17.5px;color:var(--muted)}
.about-art{left:660px;top:731px;width:540px;height:363px;background:linear-gradient(135deg,#cddc00,#b9c800 60%,#a9b800);clip-path:polygon(20% 0,100% 0,100% 100%,0 100%)}
/* band */
.band{left:0;width:1200px;background:linear-gradient(170deg,#1a2838,#2e3d4d 50%,#4a4232 80%,#2a2a22)}
.watermark{left:110px;top:1300px;font-family:"Orbitron",sans-serif;font-weight:800;font-size:92px;color:#ececec;letter-spacing:8px;transform:rotate(-6deg);transform-origin:left}
/* projects */
.section-title{left:0;width:1200px;text-align:center;font-size:32px}
.section-sub{left:0;width:1200px;text-align:center;font-size:11.5px;line-height:17px;color:var(--muted)}
/* contact */
.contact-title{font-size:33px;color:var(--white)}
.contact-item{left:180px;display:flex;gap:14px;color:var(--white)}
.icon{width:38px;height:38px;border-radius:50%;background:var(--lime);display:flex;align-items:center;justify-content:center;flex:none}
.contact-item h4{font-size:11px;font-weight:500}
.contact-item p{font-size:11px;line-height:17px}
.contact-item p.big{font-size:14px}
.divider{left:180px;width:300px;height:1px;background:rgba(255,255,255,.25)}
.quote{left:584px;top:3272px;width:488px;height:512px;background:var(--lime)}
.label{position:absolute;font-size:11px;font-weight:500}
.field{position:absolute;background:var(--white);font-size:10px;color:#666;padding-left:12px;display:flex;align-items:center}
/* footer */
.footer-rule{left:180px;top:3969px;width:840px;height:1px;background:#e3e3e3}
.copyright{left:0;top:3988px;width:1200px;text-align:center;font-size:11px;color:var(--muted)}
</style>
</head>
<body>

<!-- Hero -->
<div class="abs hero" role="img" aria-label="Excavator working on a construction site"></div>
<div class="abs header"></div>
<div class="brand" style="left:72px;top:30px"><span class="mark"></span>Bluegum Ridge Earthworks</div>
<nav class="nav" style="left:477px;top:37px"><span>Home</span><span>About</span><span>Projects</span><span>Contact Us</span></nav>
<div class="btn lime" style="left:964px;top:25px;width:164px;height:38px">Get a Quote</div>

<h1 class="abs display hero-title" style="top:238px">Moving Earth.<br>Building Foundations.</h1>
<p class="abs hero-sub" style="top:334px">Providing expert earthworks, excavation, and site preparation services with precision, safety, and efficiency.</p>
<div class="btn lime" style="left:434px;top:367px;width:164px;height:36px">Get a Quote</div>
<div class="btn white" style="left:603px;top:367px;width:164px;height:36px">View Our Projects</div>

<!-- About -->
<h2 class="abs display about-title">About<br>Bluegum Ridge</h2>
<div class="abs about-rule"></div>
<p class="abs about-text" style="top:856px">Founded in Perth, Western Australia, Bluegum Ridge Earthworks brings together decades of experience in the excavation and earthmoving industry. Our team of certified operators and project managers are committed to delivering exceptional results for every client.</p>
<p class="abs about-text" style="top:961px">We pride ourselves on our commitment to safety, environmental responsibility, and customer satisfaction. Using state-of-the-art equipment and proven techniques, we tackle projects ranging from small residential jobs to large-scale commercial developments.</p>
<div class="btn lime" style="left:180px;top:1070px;width:156px;height:38px">About Us</div>
<div class="abs about-art" role="img" aria-label="Excavator on site in lime tone"></div>

<!-- Band with loader -->
<div class="abs watermark">Bluegum Ridge</div>
<div class="abs band" style="top:1352px;height:604px;clip-path:polygon(0 18%,100% 0,100% 89.2%,0 100%)" role="img" aria-label="Fleet of earthmoving machines under a stormy sky"></div>
<div class="photo" style="left:352px;top:1195px;width:570px;height:321px;background:linear-gradient(180deg,#e0a820,#c78c10 55%,#3a3a3a);clip-path:polygon(10% 10%,40% 0,60% 35%,100% 75%,95% 100%,5% 100%)" role="img" aria-label="Yellow wheel loader"></div>
<h2 class="abs display hero-title" style="top:1590px">Moving Earth.<br>Building Foundations.</h2>
<p class="abs hero-sub" style="top:1688px">Providing expert earthworks, excavation, and site preparation services with precision, safety, and efficiency.</p>
<div class="btn lime" style="left:434px;top:1719px;width:164px;height:37px">Get a Quote</div>
<div class="btn white" style="left:603px;top:1719px;width:164px;height:37px">View Our Projects</div>

<!-- Projects -->
<h2 class="abs display section-title" style="top:2005px">Recent Projects</h2>
<p class="abs section-sub" style="top:2050px">Take a look at some of our recent earthworks and excavation projects<br>across Perth and Western Australia.</p>
<div class="photo" style="left:114px;top:2123px;width:230px;height:311px;background:linear-gradient(160deg,#c9981e,#6e5a3e 50%,#8a7358)" role="img" aria-label="Excavator tracks in mud"></div>
<div class="photo" style="left:362px;top:2123px;width:476px;height:311px;background:linear-gradient(180deg,#55585c,#6a6a66 45%,#b37a22 70%,#3a3630)" role="img" aria-label="Bulldozer front view"></div>
<div class="photo" style="left:856px;top:2123px;width:230px;height:311px;background:linear-gradient(200deg,#8b8276,#c9a03a 45%,#6d6458)" role="img" aria-label="Excavator clearing a site"></div>
<div class="photo" style="left:114px;top:2455px;width:475px;height:311px;background:linear-gradient(180deg,#b8c3c8,#c6853a 50%,#c4a98a)" role="img" aria-label="Excavators on a sandy site"></div>
<div class="photo" style="left:608px;top:2455px;width:230px;height:311px;background:linear-gradient(180deg,#a7a9ab,#5d5750 45%,#3a3732)" role="img" aria-label="Excavator at a quarry face"></div>
<div class="photo" style="left:856px;top:2455px;width:230px;height:311px;background:linear-gradient(180deg,#9aa2a8,#b89440 45%,#a68868)" role="img" aria-label="Line of dozers on cleared land"></div>
<div class="btn lime" style="left:509px;top:2791px;width:180px;height:39px">View Our Projects</div>

<!-- Contact band -->
<div class="abs band" style="top:3039px;height:750px;clip-path:polygon(0 18.8%,100% 0,100% 85.5%,0 100%)" role="img" aria-label="Excavator and truck at dusk"></div>
<div class="photo" style="left:359px;top:2922px;width:485px;height:250px;background:linear-gradient(180deg,#f2c21a,#e0a812 60%,#4a4a44);clip-path:polygon(8% 20%,55% 0,90% 30%,100% 70%,95% 100%,5% 100%)" role="img" aria-label="Yellow haul truck"></div>

<h2 class="abs display contact-title" style="left:180px;top:3310px">Contact Us</h2>
<p class="abs" style="left:180px;top:3356px;width:320px;font-size:11px;line-height:17px;color:#fff">Ready to start your earthworks project? Get in touch with our team for a free, no-obligation quote.</p>

<div class="abs contact-item" style="top:3422px">
  <span class="icon"><svg width="16" height="16" viewBox="0 0 24 24"><path d="M12 2a7 7 0 0 0-7 7c0 5 7 13 7 13s7-8 7-13a7 7 0 0 0-7-7zm0 9.5A2.5 2.5 0 1 1 12 6.5a2.5 2.5 0 0 1 0 5z" fill="#111"/></svg></span>
  <div><h4>Location</h4><p>Perth, Western Australia<br>Serving the greater Perth region and beyond</p></div>
</div>
<div class="abs divider" style="top:3496px"></div>
<div class="abs contact-item" style="top:3516px">
  <span class="icon"><svg width="15" height="15" viewBox="0 0 24 24"><path d="M6.6 10.8a15 15 0 0 0 6.6 6.6l2.2-2.2a1 1 0 0 1 1-.25 11.4 11.4 0 0 0 3.6.57 1 1 0 0 1 1 1V20a1 1 0 0 1-1 1A17 17 0 0 1 3 4a1 1 0 0 1 1-1h3.5a1 1 0 0 1 1 1c0 1.25.2 2.45.57 3.6a1 1 0 0 1-.25 1z" fill="#111"/></svg></span>
  <div><h4>Phone</h4><p class="big">(08) 9000 2716</p></div>
</div>
<div class="abs divider" style="top:3572px"></div>
<div class="abs contact-item" style="top:3594px">
  <span class="icon"><svg width="15" height="15" viewBox="0 0 24 24"><path d="M3 5h18v14H3z" fill="#111"/><path d="M3 5l9 7 9-7" stroke="#cddc00" stroke-width="1.8" fill="none"/></svg></span>
  <div><h4>Email</h4><p class="big">info@bluegumridgeearthworks.com.au</p></div>
</div>
<div class="abs divider" style="top:3650px"></div>
<div class="abs contact-item" style="top:3672px">
  <span class="icon"><svg width="16" height="16" viewBox="0 0 24 24"><circle cx="12" cy="12" r="9" fill="#111"/><path d="M12 7v5l3 2" stroke="#cddc00" stroke-width="2" fill="none"/></svg></span>
  <div><h4>Business Hours</h4><p>Monday - Friday: 7:00 AM - 5:00 PM<br>Saturday: 8:00 AM - 12:00 PM<br>Emergency services available</p></div>
</div>

<!-- Quote form -->
<div class="abs quote"></div>
<h2 class="abs display" style="left:634px;top:3312px;font-size:33px">Get a Quote</h2>
<p class="abs" style="left:634px;top:3358px;width:320px;font-size:11px;line-height:17px;color:#333">Ready to start your earthworks project? Get in touch with our team for a free, no-obligation quote.</p>
<span class="label" style="left:634px;top:3410px">Full Name</span>
<span class="label" style="left:834px;top:3410px">Email Address</span>
<div class="field" style="left:634px;top:3430px;width:188px;height:37px">Enter your name</div>
<div class="field" style="left:834px;top:3430px;width:188px;height:37px">Enter email</div>
<span class="label" style="left:634px;top:3479px">Phone Number</span>
<span class="label" style="left:834px;top:3479px">Service Required</span>
<div class="field" style="left:634px;top:3500px;width:188px;height:37px">Phone number</div>
<div class="field" style="left:834px;top:3500px;width:188px;height:37px;justify-content:space-between;padding-right:12px">Select a service<svg width="9" height="6" viewBox="0 0 9 6"><path d="M1 1l3.5 3.5L8 1" stroke="#111" stroke-width="1.4" fill="none"/></svg></div>
<span class="label" style="left:634px;top:3549px">Project Details</span>
<div class="field" style="left:634px;top:3569px;width:388px;height:112px"></div>
<div class="btn black" style="left:634px;top:3697px;width:388px;height:37px">Get a Quote</div>

<!-- Footer -->
<div class="brand" style="left:180px;top:3885px"><span class="mark"></span>Bluegum Ridge Earthworks</div>
<nav class="nav" style="left:477px;top:3891px"><span>Home</span><span>About</span><span>Projects</span><span>Contact Us</span></nav>
<div class="btn lime" style="left:844px;top:3878px;width:175px;height:39px">Get a Quote</div>
<div class="abs footer-rule"></div>
<p class="abs copyright">Copyright © 2026 Bluegum Ridge. All Rights Reserved.</p>

</body>
</html>
```